CM Candle Tube Packaging Design

Website: www.corvelmare.example
IG: @corvel.mare
Tagline: Elevate Your Ambiance
My brand is a sophisticated brand with luxury candles made of coconut wax. Im looking for an upscale minimalist chic design.
Discover the transformative power of positive energy with Corvel Mare candles. Indulge in true luxury with our specially crafted coconut wax blend that not only ignites captivating scents but also embodies modern elegance and empowering elements.
At Corvel Mare we're committed to delivering a unique and exhilarating aromatic experience to all candle lovers. Each candle is meticulously handcrafted in small batches using luxury fragrance oils exclusively formulated for coconut wax.
Our candles are:
Clean-burning
Paraben-Free
Phthalate-Free
Skin-Safe
Pet-Friendly

```html
<!DOCTYPE html>
<html lang="en">
<head>
<meta charset="utf-8">
<title>Corvel Mare – Candle Tube Label</title>
<link rel="stylesheet" href="https://fonts.googleapis.com/css2?family=Lato:wght@300&family=Dancing+Script:wght@500&display=swap">
<style>
  :root {
    --backdrop: #f6ddd3;
    --label-pink: #ebb9b7;
    --ink-white: #ffffff;
    --label-shadow: rgba(120, 70, 60, 0.35);
  }
  * { margin: 0; padding: 0; box-sizing: border-box; }
  html, body {
    width: 1200px;
    height: 723px;
    overflow: hidden;
    background: var(--backdrop);
  }
  .canvas {
    position: relative;
    width: 1200px;
    height: 723px;
    background: var(--backdrop);
  }
  .tube-label {
    position: absolute;
    left: 405px;
    top: 37px;
    width: 390px;
    height: 648px;
    background: var(--label-pink);
    box-shadow: 2px 2px 4px var(--label-shadow);
    color: var(--ink-white);
    text-align: center;
  }
  .brand-name {
    position: absolute;
    top: 48px;
    left: 0;
    width: 100%;
    font-family: "Lato", sans-serif;
    font-weight: 300;
    font-size: 38px;
    letter-spacing: 1px;
    text-transform: uppercase;
    line-height: 1;
  }
  .monogram {
    position: absolute;
    top: 232px;
    left: 0;
    width: 100%;
    font-family: "Lato", sans-serif;
    font-weight: 300;
    font-size: 52px;
    line-height: 1;
  }
  .tagline {
    position: absolute;
    top: 322px;
    left: 0;
    width: 100%;
    font-family: "Dancing Script", cursive;
    font-weight: 500;
    font-size: 24px;
    line-height: 1;
  }
  .benefits {
    position: absolute;
    top: 588px;
    left: 0;
    width: 100%;
    font-family: "Lato", sans-serif;
    font-weight: 300;
    font-size: 14.5px;
    line-height: 18px;
    list-style: none;
  }
  .benefits-row { display: block; }
  .benefit { display: inline-block; margin: 0 4px; }
  .benefit::before { content: "\2022"; margin-right: 5px; }
</style>
</head>
<body>
  <main class="canvas">
    <section class="tube-label">
      <h1 class="brand-name">Corvel Mare</h1>
      <div class="monogram">CM</div>
      <p class="tagline">Elevate your Ambiance</p>
      <ul class="benefits">
        <li class="benefits-row">
          <span class="benefit">Clean Burning</span>
          <span class="benefit">Paraben Free</span>
          <span class="benefit">Phthalate Free</span>
        </li>
        <li class="benefits-row">
          <span class="benefit">Skin Safe</span>
          <span class="benefit">Pet Friendly</span>
        </li>
      </ul>
    </section>
  </main>
</body>
</html>
```